Website for Torvel Capital - investment banking firm

We have a corporate identity (thanks to Ravinka/31842) and want to extend that into a website design.  See the attached zipped files.
We have software folks in-house to do the coding.
See the attached Project Brief & Notes for more details.  Don't worry about the actual text - lorem ipsum will be fine.
The server will be Apache.
Thank you!
Desmond

Industry/Entity Type
Investment

```html
<!DOCTYPE html>
<html lang="en">
<head>
<meta charset="utf-8">
<title>Torvel Capital – Investment Banking</title>
<link href="https://fonts.googleapis.com/css2?family=Open+Sans:wght@400;600;700&display=swap" rel="stylesheet">
<style>
:root{
  --navy:#1f3f8f;
  --navy-dark:#16306f;
  --blue-text:#1e4a9a;
  --ink:#333a44;
  --muted:#7a808a;
  --band:#eeeff1;
  --orange:#f0a23a;
  --white:#ffffff;
  --bar:#142a63;
}
*{box-sizing:border-box;margin:0;padding:0}
html,body{width:793px;height:1200px;overflow:hidden;background:var(--white)}
body{font-family:"Open Sans",Arial,sans-serif;color:var(--ink);font-size:7px;line-height:1.55}
.site-header{height:52px;background:var(--navy);display:flex;align-items:center;padding:0 40px 0 46px;justify-content:space-between}
.brand{display:flex;align-items:center;gap:7px;color:var(--white);font-weight:700;font-size:15px;letter-spacing:.3px}
.brand-mark{width:16px;height:16px;background:var(--white);display:block}
.main-nav{display:flex;gap:22px}
.main-nav a{color:var(--white);text-decoration:none;font-size:7px;font-weight:600;letter-spacing:.3px}
.hero{position:relative;height:293px;background:linear-gradient(100deg,#c9d2dc 0%,#e9ecef 40%,#b7a58f 75%,#d8c3ae 100%)}
.hero-arrow{position:absolute;top:132px;width:20px;height:24px;background:var(--navy);display:flex;align-items:center;justify-content:center}
.hero-arrow.prev{left:0}.hero-arrow.next{right:0}
.section-title{color:var(--blue-text);font-size:12px;font-weight:700;margin-bottom:10px}
.welcome{height:195px;padding:30px 40px 0;display:flex;gap:24px}
.welcome p{width:565px;color:var(--muted)}
.welcome-photo{width:110px;height:80px;margin-top:28px;background:linear-gradient(135deg,#e4e6ea,#c8ccd2)}
.services{height:185px;background:var(--band);padding:30px 40px 0;display:flex;gap:52px}
.tablet{width:170px;height:125px;background:#1a1a1a;border-radius:10px;padding:9px 12px}
.tablet div{width:100%;height:100%;background:linear-gradient(120deg,#d9c1a8,#8aa0b8)}
.services-copy{padding-top:10px;width:490px}
.services-copy p{color:var(--muted);margin-bottom:12px}
.btn{display:inline-block;background:var(--navy);color:var(--white);font-size:7px;font-weight:700;padding:6px 14px}
.transactions{height:145px;padding:22px 40px 0}
.row-head{display:flex;justify-content:space-between;align-items:center;width:640px}
.mini-arrows{display:flex;gap:4px}
.mini-arrows span{width:11px;height:11px;border-radius:50%;background:#c9ccd1;display:block}
.cards{display:flex;gap:30px;margin-top:4px}
.card{width:130px}
.card-tag{background:var(--orange);color:var(--white);font-size:6px;text-align:center;padding:3px 0;font-weight:600}
.card-body{height:46px;border:1px solid #e1e3e6;display:flex;flex-direction:column;align-items:center;justify-content:center;gap:2px}
.card-name{font-weight:700;font-size:10px;color:var(--ink)}
.card-body small{font-size:5.5px;color:var(--muted)}
.testimonials{height:145px;padding:10px 40px 0;border-top:1px solid #eceef0}
.quotes{display:flex;gap:40px;margin-top:14px}
.quote{display:flex;gap:14px;width:330px}
.avatar{width:34px;height:34px;border-radius:50%;flex:none;background:linear-gradient(135deg,#9aa6b6,#e2e5ea)}
.quote p{color:var(--muted);font-style:normal}
.quote b{display:block;color:var(--ink);font-size:7px;margin-top:7px}
.quote small{color:var(--muted);font-size:6px}
.site-footer{height:150px;background:var(--navy);padding:20px 40px 0;display:flex;gap:60px;color:#dce4f4}
.site-footer h4{color:var(--white);font-size:10px;font-weight:600;margin-bottom:6px}
.site-footer ul{list-style:none}
.footer-contact{width:210px}
.map{width:200px;height:96px;background:linear-gradient(135deg,#dfe4d8,#c9d4e2)}
.bottom-bar{height:35px;background:var(--bar);display:flex;align-items:center;justify-content:center;color:#aab6d2;font-size:6px;position:relative}
.bottom-bar span.top{position:absolute;right:40px}
</style>
</head>
<body>
<header class="site-header">
  <div class="brand"><span class="brand-mark"></span>TORVEL CAPITAL</div>
  <nav class="main-nav"><a href="#">HOME</a><a href="#">ABOUT</a><a href="#">SERVICES</a><a href="#">CURRENT TRANSACTIONS</a><a href="#">COMPLETED TRANSACTIONS</a></nav>
</header>

<section class="hero" role="img" aria-label="Photo of a smiling businesswoman with a headset in a bright office with colleagues">
  <span class="hero-arrow prev"><svg width="8" height="10" viewBox="0 0 8 10"><path d="M6 1 2 5l4 4" stroke="#fff" stroke-width="1.6" fill="none"/></svg></span>
  <span class="hero-arrow next"><svg width="8" height="10" viewBox="0 0 8 10"><path d="M2 1l4 4-4 4" stroke="#fff" stroke-width="1.6" fill="none"/></svg></span>
</section>

<section class="welcome">
  <div>
    <h2 class="section-title">Welcome to TORVEL</h2>
    <p>Lorem ipsum dolor sit amet, consectetur adipiscing elit. Aliquam id nisl sit amet mauris porttitor at sit a massa. Vestibulum aliquet urna non ligula tincidunt, quis volutpat dui consequat. Quisque lectus mauris, blandit sed pulvinar vitae, tempus at nisi. Nullam vehicula nisi eget sem dictum, ac faucibus leo molestie. Donec suscipit mi eu urna dignissim, nec facilisis lorem convallis. Morbi dapibus nunc eget turpis hendrerit, vitae vestibulum ex accumsan. Integer malesuada lectus non velit porta, eget luctus ante fringilla. Praesent eu tortor sed massa aliquam fermentum in ac nunc. Sed ultricies felis at consequat posuere. Maecenas viverra augue a nibh tempor, quis gravida nisl feugiat. Curabitur sodales ipsum non orci sagittis, sit amet dictum urna tincidunt. Etiam bibendum velit nec arcu interdum, id volutpat purus rutrum. Nunc scelerisque sapien vel ex ultricies, a posuere risus convallis. Fusce tempor magna sed lorem hendrerit ultrices.</p>
  </div>
  <div class="welcome-photo" role="img" aria-label="Photo of a customer service agent wearing a headset"></div>
</section>

<section class="services">
  <div class="tablet"><div role="img" aria-label="Tablet screen showing a photo of a smiling team"></div></div>
  <div class="services-copy">
    <h2 class="section-title">Our Services</h2>
    <p>Torvel Capital advises growing companies on mergers, acquisitions and capital raising. Our team combines deep sector knowledge with a personal approach, guiding clients from first strategy to closing. We work across markets to match each business with the right partners and structure every transaction around long term value for owners, investors and employees.</p>
    <span class="btn">READ MORE</span>
  </div>
</section>

<section class="transactions">
  <div class="row-head"><h2 class="section-title">Previous Transactions</h2><div class="mini-arrows"><span></span><span></span></div></div>
  <div class="cards">
    <div class="card"><div class="card-tag">Sale Advisory</div><div class="card-body"><span class="card-name">Harbor Cove</span><small>Hotel Group, Inc.</small></div></div>
    <div class="card"><div class="card-tag">Sale Advisory</div><div class="card-body"><span class="card-name">Fornello</span><small>Austin, TX</small></div></div>
    <div class="card"><div class="card-tag">Sale Advisory</div><div class="card-body"><span class="card-name">Marlow &amp; Pike</span><small>Dallas, TX</small></div></div>
    <div class="card"><div class="card-tag">Sale Advisory</div><div class="card-body"><span class="card-name">Quilla Foods</span><small>Houston, TX</small></div></div>
  </div>
</section>

<section class="testimonials">
  <div class="row-head"><h2 class="section-title">What Our Customer Says</h2><div class="mini-arrows"><span></span><span></span></div></div>
  <div class="quotes">
    <div class="quote"><span class="avatar" role="img" aria-label="Portrait photo of a client"></span><div><p>"Nullam blandit orci, viverra gravida nisi lobortis eget. Maecenas fringilla arcu ac nisi scelerisque facilisis sapien, non viverra gravida nisl rhoncus eget."</p><b>ELENA MARSH</b><small>President</small></div></div>
    <div class="quote"><span class="avatar" role="img" aria-label="Portrait photo of a client"></span><div><p>"Nullam blandit orci, viverra gravida nisi lobortis eget. Maecenas fringilla arcu ac nisi scelerisque facilisis sapien, non viverra gravida nisl rhoncus eget."</p><b>DANIEL OKAFOR</b><small>President</small></div></div>
  </div>
</section>

<footer class="site-footer">
  <div class="footer-contact"><h4>Contact Us</h4><p>Harbour Point Tower, 21st Floor<br>18 Crescent Road, Westbay<br>Telephone +00 000 0000<br><br>Dallas Office, Suite 450<br>220 Linden Avenue, Plano, TX<br>Telephone +00 000 0000</p></div>
  <div><h4>Links</h4><ul><li>Home</li><li>About</li><li>Services</li><li>Current Engagements</li><li>Completed Transactions</li></ul></div>
  <div><h4>Location</h4><div class="map" role="img" aria-label="Map showing the office location"></div></div>
</footer>
<div class="bottom-bar">© Copyright 2014 Torvel Capital · All Rights Reserved<span class="top">TOP</span></div>
</body>
</html>
```